Core Values Banner For Hearthwell Guards Inc

We want to take the core values for our small growing chimney service company and post them for our entire team to see on a daily basis. We want to be remind everyone how important this is too us all. IntegrityWe try to be honest and accountable in all aspects of our business, as well as in our personal interactions. We do what we say we will do, when we say we will do it, and how we say we will do it.Kaizen“Change for the best”We strive to constantly grow and improve, both personally and professionally. We own up to our mistakes and strive to resolve and learn from them. We actively seek feedback from our clients and each other. We believe the most innovative ideas come when we intentionally look for them.FamilyWe are a family-owned business, and we consider everyone who works here and every one we serve to be part of the family. Being honest and genuine with each other and our customers is what sets us apart. We put ourselves in our customer’s shoes and make recommendations as if it were our chimney, our home and our family.

Font styles to use
Serif
Sans Serif

Colors
ec1f27

Requirements
Must have
• This banner will be approximately 2.5' in height and 6 to 6.5' in width.
• I would like all 3 core values and there definitions listed on the banner
• check out the feel of our marketing on our website www.hearthwellguardsnx.com

```html
<!DOCTYPE html>
<html lang="en">
<head>
<meta charset="utf-8">
<title>Hearthwell Guards Inc — Core Values Banner</title>
<link href="https://fonts.googleapis.com/css2?family=Lato:wght@400;700&display=swap" rel="stylesheet">
<style>
  :root {
    --banner-red: #c9203b;
    --ink-white: #ffffff;
    --backdrop: #efefef;
    --rule: 4px;
  }
  * { margin: 0; padding: 0; box-sizing: border-box; }
  html, body {
    width: 1200px;
    height: 534px;
    overflow: hidden;
    background: var(--backdrop);
    font-family: "Lato", sans-serif;
    color: var(--ink-white);
  }
  .banner {
    position: absolute;
    left: 20px;
    top: 45px;
    width: 1160px;
    height: 444px;
    background: var(--banner-red);
  }
  .frame-line {
    position: absolute;
    background: var(--ink-white);
  }
  .frame-top-left     { left: 44px;  top: 47px;  width: 382px; height: var(--rule); }
  .frame-top-right    { left: 730px; top: 47px;  width: 390px; height: var(--rule); }
  .frame-left         { left: 44px;  top: 47px;  width: var(--rule); height: 355px; }
  .frame-right        { left: 1116px; top: 47px; width: var(--rule); height: 355px; }
  .frame-bottom-left  { left: 44px;  top: 398px; width: 479px; height: var(--rule); }
  .frame-bottom-right { left: 633px; top: 398px; width: 487px; height: var(--rule); }

  .frame-mark {
    position: absolute;
    left: 560px;
    top: 380px;
    width: 40px;
    height: 40px;
    background: var(--ink-white);
  }

  .banner-title {
    position: absolute;
    left: 0;
    width: 100%;
    top: 22px;
    text-align: center;
    font-weight: 700;
    font-size: 48px;
    line-height: 56px;
  }

  .column-divider {
    position: absolute;
    top: 131px;
    width: 3px;
    height: 203px;
    background: var(--ink-white);
  }
  .divider-one { left: 401px; }
  .divider-two { left: 759px; }

  .value {
    position: absolute;
    text-align: center;
  }
  .value-integrity { left: 101px; width: 258px; top: 112px; }
  .value-kaizen    { left: 450px; width: 266px; top: 103px; }
  .value-family    { left: 800px; width: 258px; top: 112px; }

  .value-name {
    font-weight: 700;
    font-size: 48px;
    line-height: 60px;
    white-space: nowrap;
  }
  .value-kaizen .value-name { line-height: 52px; }
  .value-tagline {
    font-weight: 700;
    font-size: 21px;
    line-height: 26px;
  }
  .value-text {
    font-weight: 400;
    font-size: 13.6px;
    line-height: 19.4px;
    margin-top: 40px;
  }
  .value-kaizen .value-text {
    margin-top: 31px;
    text-align: justify;
    text-align-last: center;
  }
  .value-family .value-text {
    text-align: justify;
    text-align-last: center;
  }
</style>
</head>
<body>
  <main class="banner" aria-label="Hearthwell Guards Inc core values">
    <div class="frame-line frame-top-left"></div>
    <div class="frame-line frame-top-right"></div>
    <div class="frame-line frame-left"></div>
    <div class="frame-line frame-right"></div>
    <div class="frame-line frame-bottom-left"></div>
    <div class="frame-line frame-bottom-right"></div>
    <div class="frame-mark" aria-hidden="true"></div>

    <h1 class="banner-title">Core Values</h1>

    <div class="column-divider divider-one"></div>
    <div class="column-divider divider-two"></div>

    <section class="value value-integrity">
      <h2 class="value-name">Integrity</h2>
      <p class="value-text">We try to be honest and accountable in all aspects of our business, as well as in our personal interactions. We do what we say we will do, when we say we will do it, and how we say we will do it.</p>
    </section>

    <section class="value value-kaizen">
      <h2 class="value-name">Kaizen</h2>
      <p class="value-tagline">“Change for the best”</p>
      <p class="value-text">We strive to constantly grow and improve, both personally and professionally. We own up to our mistakes and strive to resolve and learn from them. We actively seek feedback from our clients and each other. We believe the most innovative ideas come when we intentionally look for them.</p>
    </section>

    <section class="value value-family">
      <h2 class="value-name">Family</h2>
      <p class="value-text">We are a family-owned business, and we consider everyone who works here and every one we serve to be part of the family. Being honest and genuine with each other and our customers is what sets us apart. We put ourselves in our customer’s shoes and make recommendations as if it were our chimney, our home and our family.</p>
    </section>
  </main>
</body>
</html>
```